Maple Grove Schools | brand new stationery!

We need stationery design with our new logo! Our company updated it's name and image and we like to incorporate the new one on our stationery, business cards and email signature. We are looking for fresh, new ideas!
Industry: Childcare, Elementary and Middle School
Company Name: Maple Grove Schools
Tagline: Bright Futures Start Here
Main colors: Blue, white and a little yellow
Star shape is something new for us! Do you see a way to incorporate it as a design element?

```html
<!DOCTYPE html>
<html lang="en">
<head>
<meta charset="utf-8">
<title>Maple Grove Schools – Business Card</title>
<link href="https://fonts.googleapis.com/css2?family=Poppins:wght@400;500;700&family=Roboto:wght@400&display=swap" rel="stylesheet">
<style>
  :root {
    --navy: #061c6c;
    --yellow: #f7c325;
    --white: #ffffff;
    --ink: #1d1d1f;
    --text: #2a2a2e;
    --backdrop: #e6e7ea;
    --card-radius: 18px;
  }
  * { box-sizing: border-box; margin: 0; padding: 0; }
  html, body {
    width: 1200px; height: 874px; overflow: hidden;
    background: var(--backdrop);
  }
  .canvas { position: relative; width: 1200px; height: 874px; }
  .card {
    position: absolute; width: 640px; height: 366px;
    border-radius: var(--card-radius); overflow: hidden;
    box-shadow: 0 10px 30px rgba(0,0,0,0.18);
  }
  /* Back side */
  .card-back { left: 420px; top: 48px; background: var(--navy); }
  .card-back .brand-name {
    position: absolute; left: 0; right: 0; top: 120px; text-align: center;
    font-family: "Poppins", sans-serif; font-weight: 700; font-size: 44px;
    line-height: 1.05; color: var(--white);
  }
  .card-back .web {
    position: absolute; left: 0; right: 0; bottom: 34px; text-align: center;
    font-family: "Roboto", sans-serif; font-size: 15px; letter-spacing: 4px;
    color: var(--white); text-transform: uppercase;
  }
  /* Front side */
  .card-front { left: 140px; top: 460px; background: var(--white); }
  .card-front .brand-name {
    position: absolute; left: 44px; top: 40px;
    font-family: "Poppins", sans-serif; font-weight: 700; font-size: 34px;
    line-height: 1.05; color: var(--ink);
  }
  .contact {
    position: absolute; left: 44px; top: 142px; list-style: none;
    font-family: "Roboto", sans-serif; font-size: 15px; line-height: 21px; color: var(--text);
  }
  .contact li { display: flex; align-items: center; gap: 8px; }
  .contact .address { padding-left: 22px; }
  .contact svg { width: 14px; height: 14px; fill: var(--navy); flex: none; }
  .person {
    position: absolute; right: 48px; bottom: 78px; text-align: left;
    font-family: "Poppins", sans-serif;
  }
  .person .name { font-size: 22px; font-weight: 500; letter-spacing: 1px; color: var(--navy); text-transform: uppercase; }
  .person .role { font-size: 15px; color: var(--yellow); padding-left: 110px; margin-top: -4px; }
  .stripe { position: absolute; left: 0; bottom: 0; width: 640px; height: 22px; }
</style>
</head>
<body>
<main class="canvas">
  <section class="card card-back">
    <div class="brand-name">Maple Grove<br>Schools</div>
    <div class="web">www.maplegroveschools.com</div>
  </section>

  <section class="card card-front">
    <div class="brand-name">Maple Grove<br>Schools</div>
    <ul class="contact">
      <li class="address">214 Birchwood Avenue</li>
      <li class="address">Fairview, Oregon 97024</li>
      <li><svg viewBox="0 0 24 24"><path d="M6.6 10.8a15 15 0 0 0 6.6 6.6l2.2-2.2c.3-.3.7-.4 1-.2 1.1.4 2.3.6 3.6.6.6 0 1 .4 1 1V20c0 .6-.4 1-1 1A17 17 0 0 1 3 4c0-.6.4-1 1-1h3.5c.6 0 1 .4 1 1 0 1.3.2 2.5.6 3.6.1.3 0 .7-.2 1z"/></svg>555-304-7721</li>
      <li><svg viewBox="0 0 24 24"><path d="M7 2h10a2 2 0 0 1 2 2v16a2 2 0 0 1-2 2H7a2 2 0 0 1-2-2V4a2 2 0 0 1 2-2zm0 3v13h10V5z"/></svg>555-418-9062</li>
      <li><svg viewBox="0 0 24 24"><path d="M2 5h20v14H2zm2 2v.5l8 5 8-5V7z"/></svg>hello@maplegroveschools.com</li>
      <li><svg viewBox="0 0 24 24"><circle cx="12" cy="12" r="10"/></svg>maplegroveschools.com</li>
    </ul>
    <div class="person">
      <div class="name">Daniel Harper</div>
      <div class="role">President</div>
    </div>
    <svg class="stripe" viewBox="0 0 640 22" preserveAspectRatio="none" aria-hidden="true">
      <polygon points="0,0 390,0 404,22 0,22" fill="var(--navy)"/>
      <polygon points="396,0 640,0 640,22 410,22" fill="var(--yellow)"/>
    </svg>
  </section>
</main>
</body>
</html>
```